Luxury Real Estate Website, Midwest, United States

We need web design services for a luxury website. We need IDX Integration with our MLS. We want this to be a very simple website with amazing graphics. We want it to link up with our MailChimp account in order to generate leads through a "More Information" Pop up on the main page. We want the main page to be covered with one large graphic that is a rolling slideshow of active listings of $400,000 and up from the IDX Integration. We need this website to give a very exclusive and sleek look. Lots of black is good... I will upload our logos in Black and Silver. We will also need an "About" page that we are going to call "Qeno Info". We want our graphics to be extremely impressive. Keep in mind, we are a company in the Midwest of the United States, and our real estate has a different look than homes in California or Florida. We need graphics that are realistic for the Midwest, yet still high-end.
Target Market(s)
Luxury Homeowners in the Midwest United States. The graphics needs to be pristine.
Industry/Entity Type
Real Estate
Coding
Coded - Design and coding required
Number of Pages Required
3 page
Requirements
Must have
- Large graphics with IDX Integration. The photos of real estate need to represent real estate that is common in the Midwest, United States. We also need MailChimp integration. We need a pop up that is titled "My Free Market Analysis" that makes them fill out a contact form asking for Full Name, Email Address, Phone Number and Address. This needs to be a pop up on the front page and will integrate with our MailChimp account. We also need a page called "About Qe No Home". And another page where clients can download informational PDFs. The main component needs to be a front page search engine connected with the IDX to access active listings from our MLS. I attached our logos and a sample front page of a website. I would love for ours to look similar.
Nice to have
- Lake House photos on midwest lakes are a plus.
Should not have
- Should not have clutter. This website needs to be clean, luxurious and exclusive.

```html
<!DOCTYPE html>
<html lang="en">
<head>
<meta charset="utf-8">
<title>Ashwood Realty Group</title>
<link rel="stylesheet" href="https://fonts.googleapis.com/css2?family=Josefin+Sans:wght@300;400;600&family=Open+Sans:ital,wght@0,400;0,600;0,700;1,600&display=swap">
<style>
:root{
  --ink:#222;
  --muted:#7a7a7a;
  --line:#d6d6d6;
  --accent:#b7c6da;
  --accent-dark:#8fa3bf;
  --tab:#5b8fd6;
  --white:#fff;
  --footer:#1b1c1e;
  --footer-line:#3a3b3e;
}
*{box-sizing:border-box;margin:0;padding:0}
html,body{width:1200px;height:3488px;overflow:hidden;background:var(--white)}
body{position:relative;font-family:"Open Sans",sans-serif;color:var(--ink)}
.abs{position:absolute}
.heading{font-family:"Josefin Sans",sans-serif;font-weight:400;letter-spacing:1px}

/* hero */
.hero{left:0;top:0;width:1200px;height:635px;background:linear-gradient(180deg,#4f74b8 0%,#7d9bd0 38%,#8e9aa8 58%,#3f5a2c 72%,#2a3320 86%,#1c2326 100%)}
.logo{left:98px;top:40px;color:var(--white);font-family:"Josefin Sans",sans-serif;font-weight:400;font-size:34px;letter-spacing:2px;display:flex;align-items:center;gap:14px}
.logo-mark{width:14px;height:14px;background:var(--white)}
.phone{left:795px;top:24px;color:var(--white);font-size:20px;display:flex;align-items:center;gap:10px}
.login{left:993px;top:12px;width:108px;height:44px;border:2px solid var(--white);border-radius:22px;color:var(--white);font-size:15px;font-weight:600;display:flex;align-items:center;justify-content:center;gap:8px}
.nav{left:457px;top:76px;display:flex;gap:38px;color:var(--white);font-size:15px;align-items:center}
.nav .active{border-bottom:1px solid var(--white);padding-bottom:2px}
.side-tab{width:40px;height:150px;background:var(--tab);color:var(--white);font-size:15px;font-weight:700;writing-mode:vertical-rl;display:flex;align-items:center;justify-content:center;letter-spacing:1px}
.tab-left{left:0;top:215px;transform:rotate(180deg);border-radius:0 6px 6px 0}
.tab-right{left:1160px;top:215px;border-radius:6px 0 0 6px}
.tagline{left:0;top:508px;width:1200px;text-align:center;color:var(--white);font-size:33px;font-weight:300}
.search{left:260px;top:564px;width:680px;height:46px;background:var(--white);display:flex;align-items:center}
.search span{flex:1;padding-left:20px;font-size:14px;color:#555;display:flex;align-items:center;gap:8px}
.search-btn{width:46px;height:46px;background:#c7d0dc;display:flex;align-items:center;justify-content:center}

/* welcome */
.welcome-bar{left:100px;top:790px;width:5px;height:78px;background:var(--accent)}
.welcome-title{left:122px;top:782px;width:430px;font-size:32px;line-height:48px;letter-spacing:.5px;color:#333;white-space:nowrap}
.welcome-copy{left:572px;top:706px;width:530px;font-size:13px;line-height:29px;color:var(--muted)}
.btn-outline{height:44px;width:136px;border:2px solid var(--line);border-radius:22px;font-size:13px;font-weight:700;color:#999;display:flex;align-items:center;justify-content:center;letter-spacing:1px}

/* features */
.features{left:0;top:1040px;width:1200px;height:237px;background:var(--accent)}
.feature{top:1088px;width:320px;color:var(--white)}
.feature h3{font-family:"Josefin Sans",sans-serif;font-weight:400;font-size:23px;margin:24px 0 6px}
.feature p{font-size:13px;line-height:20px;opacity:.9}
.divider{top:1100px;width:1px;height:125px;background:rgba(255,255,255,.5)}

/* services */
.section-title{left:0;width:1200px;text-align:center;font-size:35px;color:#222}
.card{top:1440px;width:233px;height:232px;border:1px solid var(--line);text-align:center;padding-top:30px}
.card-icon{height:56px;display:flex;align-items:center;justify-content:center}
.card h4{font-size:18px;font-weight:600;margin:22px 0 12px;color:#222;white-space:nowrap}
.card p{font-size:12.5px;line-height:22px;color:var(--muted);padding:0 12px}

/* testimonial */
.testimonial{left:0;top:1763px;width:1200px;height:516px;background:linear-gradient(100deg,#4a5546 0%,#6d7a64 35%,#8a9a72 60%,#5d8a3c 85%,#4f7a30 100%)}
.quote{left:98px;top:1955px;width:460px;color:var(--white);font-size:17px;font-weight:600;font-style:italic;line-height:31px}
.author{left:98px;top:2172px;color:var(--white);font-weight:700;font-size:18px;letter-spacing:1px}

/* properties */
.property{top:2433px;width:295px;height:258px}

/* footer */
.footer{left:0;top:2875px;width:1200px;height:613px;background:var(--footer)}
.label{color:var(--white);font-size:11px;letter-spacing:1px}
.col-title{color:var(--white);font-size:15px;font-weight:700}
.field{left:100px;width:628px;background:var(--white)}
.submit{left:643px;top:3320px;width:87px;height:40px;background:var(--accent);color:var(--white);font-size:13px;font-weight:700;display:flex;align-items:center;justify-content:center;letter-spacing:1px}
.info-icon{left:810px;width:34px;height:34px;border:1.5px solid #cfcfcf;border-radius:50%;display:flex;align-items:center;justify-content:center}
.info-text{left:862px;color:#ddd;font-size:13px;line-height:24px}
.rule{left:98px;top:3405px;width:1004px;height:1px;background:var(--footer-line)}
.copyright{left:98px;top:3433px;color:#bbb;font-size:11px}
.social{top:3426px;width:28px;height:28px;border:1.5px solid #cfcfcf;border-radius:50%}
</style>
</head>
<body>

<!-- hero -->
<div class="abs hero" role="img" aria-label="Lakeside Midwest luxury home with shingle siding under a blue sky"></div>
<div class="abs logo"><span class="logo-mark"></span>ASHWOOD</div>
<div class="abs phone">
  <svg width="18" height="18" viewBox="0 0 24 24" fill="#fff"><path d="M6.6 10.8a15 15 0 0 0 6.6 6.6l2.2-2.2a1 1 0 0 1 1-.25 11.4 11.4 0 0 0 3.6.57 1 1 0 0 1 1 1V20a1 1 0 0 1-1 1A17 17 0 0 1 3 4a1 1 0 0 1 1-1h3.5a1 1 0 0 1 1 1c0 1.25.2 2.45.57 3.57a1 1 0 0 1-.25 1z"/></svg>
  1 555 010 0199
</div>
<div class="abs login">
  <svg width="12" height="14" viewBox="0 0 12 14" fill="#fff"><rect x="0" y="6" width="12" height="8" rx="1"/><path d="M3 6V4a3 3 0 0 1 6 0v2" fill="none" stroke="#fff" stroke-width="1.6"/></svg>
  LOGIN
</div>
<nav class="abs nav">
  <span class="active">HOME</span>
  <span>QENO INFO</span>
  <span>ABOUT QE NO HOME</span>
  <span>DOWNLOADS</span>
  <span>CONTACT US</span>
  <svg width="16" height="16" viewBox="0 0 16 16"><circle cx="6.5" cy="6.5" r="5" fill="none" stroke="#fff" stroke-width="2"/><path d="M10 10l5 5" stroke="#fff" stroke-width="2"/></svg>
</nav>
<div class="abs side-tab tab-left">FEEDBACK</div>
<div class="abs side-tab tab-right">LIVECHAT</div>
<div class="abs tagline heading">Luxury real estate company from Midwest, United states</div>
<div class="abs search">
  <span>
    <svg width="10" height="14" viewBox="0 0 10 14" fill="#333"><path d="M5 0a5 5 0 0 1 5 5c0 3.5-5 9-5 9S0 8.5 0 5a5 5 0 0 1 5-5zm0 3a2 2 0 1 0 0 4 2 2 0 0 0 0-4z"/></svg>
    Search homes by city &amp; state , zip, or MLS#
  </span>
  <div class="search-btn"><svg width="16" height="16" viewBox="0 0 16 16"><circle cx="6.5" cy="6.5" r="5" fill="none" stroke="#333" stroke-width="2"/><path d="M10 10l5 5" stroke="#333" stroke-width="2"/></svg></div>
</div>

<!-- welcome -->
<div class="abs welcome-bar"></div>
<h1 class="abs welcome-title heading">WELCOME TO<br>ASHWOOD REALTY GROUP</h1>
<p class="abs welcome-copy">Nemo enim ipsam voluptatem quia voluptas sit aspernatur aut odit aut fugit, sed quia consequuntur magni dolores eos qui ratione voluptatem sequi nesciunt neque porro quis quam est, qui dolorem ipsum quia dolor sit amet, consectetur, adipisci velit, sed quia non numquam eius modi tempora incidunt ut labore et dolore magnam aliquam quaerat voluptatem. Ut enim ad minima veniam, quis nostrum exercitationem ullam corporis suscipit et eum iure reprehenderit qui in ea.</p>
<div class="abs btn-outline" style="left:572px;top:908px">READ MORE</div>

<!-- features -->
<div class="abs features"></div>
<div class="abs feature" style="left:98px">
  <svg width="48" height="40" viewBox="0 0 48 40" fill="#fff"><path d="M2 2h18l20 20-16 16L2 18z"/><circle cx="10" cy="10" r="3" fill="#b7c6da"/><path d="M24 2h4l20 20-16 16-2-2 14-14z"/></svg>
  <h3>Sell in a few simple steps</h3>
  <p>Nemo enim ipsam voluptatem quia voluptas sit aspernatur aut odit aut fugit, sed quia.</p>
</div>
<div class="abs divider" style="left:432px"></div>
<div class="abs feature" style="left:470px">
  <svg width="40" height="40" viewBox="0 0 40 40" fill="none" stroke="#fff" stroke-width="2.5"><circle cx="20" cy="20" r="17"/><circle cx="14" cy="15" r="1.5" fill="#fff"/><circle cx="26" cy="15" r="1.5" fill="#fff"/><path d="M12 24c4 5 12 5 16 0"/></svg>
  <h3>Stress free sale</h3>
  <p>Nemo enim ipsam voluptatem quia voluptas sit aspernatur aut odit aut fugit, sed quia.</p>
</div>
<div class="abs divider" style="left:810px"></div>
<div class="abs feature" style="left:848px">
  <svg width="40" height="40" viewBox="0 0 40 40" fill="#fff"><rect x="2" y="17" width="8" height="21"/><path d="M13 18l8-14c3 0 4 2 4 4l-1 8h11c2 0 3 2 3 3l-4 16c-.5 2-2 3-4 3H13z"/></svg>
  <h3>Total certainity</h3>
  <p>Nemo enim ipsam voluptatem quia voluptas sit aspernatur aut odit aut fugit, sed quia.</p>
</div>

<!-- services -->
<h2 class="abs section-title heading" style="top:1350px">WHAT WE DO</h2>
<div class="abs card" style="left:98px">
  <div class="card-icon"><svg width="66" height="52" viewBox="0 0 66 52" fill="#b5b5b5"><rect x="2" y="48" width="62" height="3"/><rect x="2" y="2" width="3" height="48"/><rect x="12" y="26" width="7" height="20"/><rect x="24" y="14" width="7" height="32"/><rect x="36" y="22" width="7" height="24"/><rect x="48" y="30" width="7" height="16"/></svg></div>
  <h4>Permanent Financing</h4>
  <p>Nemo enim ipsam voluptatequ<br>ia volu ptas sit asperna</p>
</div>
<div class="abs card" style="left:354px">
  <div class="card-icon"><svg width="52" height="52" viewBox="0 0 52 52" fill="none" stroke="#b5b5b5" stroke-width="6"><path d="M44 20A19 19 0 0 0 9 17"/><path d="M8 32a19 19 0 0 0 35 3"/><path d="M6 6v12h12" stroke-width="5"/><path d="M46 46V34H34" stroke-width="5"/></svg></div>
  <h4>Refinance</h4>
  <p>Nemo enim ipsam voluptatequ<br>ia volu ptas sit asperna</p>
</div>
<div class="abs card" style="left:612px">
  <div class="card-icon"><svg width="62" height="52" viewBox="0 0 62 52" fill="#b5b5b5"><rect x="22" y="2" width="18" height="12"/><rect x="2" y="38" width="16" height="12"/><rect x="23" y="38" width="16" height="12"/><rect x="44" y="38" width="16" height="12"/><path d="M30 14v10M10 38V26h42v12M31 26v12" stroke="#b5b5b5" stroke-width="3" fill="none"/></svg></div>
  <h4>Acquisition Loans</h4>
  <p>Nemo enim ipsam voluptatequ<br>ia volu ptas sit asperna</p>
</div>
<div class="abs card" style="left:868px">
  <div class="card-icon"><svg width="44" height="56" viewBox="0 0 44 56" fill="#b5b5b5"><path d="M4 2h36v52H4z" fill="none" stroke="#b5b5b5" stroke-width="4"/><rect x="11" y="9" width="6" height="6"/><rect x="19" y="9" width="6" height="6"/><rect x="27" y="9" width="6" height="6"/><rect x="11" y="19" width="6" height="6"/><rect x="19" y="19" width="6" height="6"/><rect x="27" y="19" width="6" height="6"/><rect x="11" y="29" width="6" height="6"/><rect x="19" y="29" width="6" height="6"/><rect x="27" y="29" width="6" height="6"/><rect x="18" y="40" width="8" height="14"/></svg></div>
  <h4>Construction &amp; Bridge</h4>
  <p>Nemo enim ipsam voluptatequ<br>ia volu ptas sit asperna</p>
</div>

<!-- testimonial -->
<div class="abs testimonial" role="img" aria-label="Family relaxing together on a lawn in front of a modern home"></div>
<svg class="abs" style="left:98px;top:1848px" width="78" height="64" viewBox="0 0 78 64" fill="#fff"><path d="M0 64V34C0 14 8 4 30 0v12C18 16 16 22 16 30h16v34zM44 64V34C44 14 52 4 74 0v12c-12 4-14 10-14 18h16v34z"/></svg>
<p class="abs quote">“ At vero eos et accusamus et iusto odio dignissimosdu cimus qui blanditiis praesentium voluptatum deleniti atque corrupti quos dolores et quas molestias except uri sint occaecati cupiditate non provident, similique sunt in culpa qui officia deserunt mollitia animi, idest laborum et dolorum fuga.”</p>
<div class="abs author">– JANE MILLER</div>
<svg class="abs" style="left:30px;top:2006px" width="16" height="28" viewBox="0 0 16 28"><path d="M14 2L3 14l11 12" fill="none" stroke="#fff" stroke-width="3"/></svg>
<svg class="abs" style="left:1146px;top:2006px" width="16" height="28" viewBox="0 0 16 28"><path d="M2 2l11 12L2 26" fill="none" stroke="#fff" stroke-width="3"/></svg>

<!-- properties -->
<h2 class="abs section-title heading" style="top:2355px">PROPERTIES</h2>
<div class="abs property" style="left:0;background:linear-gradient(180deg,#bcd0e4 0%,#a97a55 45%,#6b5a48 70%,#4a4640 100%)" role="img" aria-label="Red lakeside cottages with birds over the water"></div>
<div class="abs property" style="left:302px;background:linear-gradient(180deg,#0d2f9e 0%,#2a52c8 35%,#6a6a3a 55%,#8a7a60 72%,#2f4f8a 100%)" role="img" aria-label="Lakefront homes among autumn trees with a marina"></div>
<div class="abs property" style="left:604px;background:linear-gradient(180deg,#3e86c8 0%,#7fb0dc 30%,#3f5a2e 52%,#5a6a5a 68%,#1f5aa0 100%)" role="img" aria-label="Lake house on a wooded shore with deep blue water"></div>
<div class="abs property" style="left:906px;width:294px;background:linear-gradient(180deg,#6fa3d8 0%,#a9c8e4 30%,#3a5a2a 55%,#7a8a7a 70%,#3f78b0 100%)" role="img" aria-label="Waterfront home with boathouse on a Midwest lake"></div>
<div class="abs btn-outline" style="left:532px;top:2743px">VIEW MORE</div>

<!-- contact -->
<div class="abs footer" role="img" aria-label="Dark aerial view of a residential neighbourhood"></div>
<h2 class="abs section-title heading" style="top:2950px;color:#fff">CONTACT</h2>
<div class="abs col-title" style="left:98px;top:3020px">CONTACT FORM</div>
<div class="abs label" style="left:100px;top:3064px">NAME :</div>
<div class="abs field" style="top:3092px;height:32px"></div>
<div class="abs label" style="left:100px;top:3133px">EMAIL :</div>
<div class="abs field" style="top:3157px;height:32px"></div>
<div class="abs label" style="left:100px;top:3198px">MESSAGE :</div>
<div class="abs field" style="top:3224px;height:82px"></div>
<div class="abs submit">SUBMIT</div>

<div class="abs col-title" style="left:808px;top:3020px">CONTACT INFORMATION</div>
<div class="abs info-icon" style="top:3080px"><svg width="10" height="14" viewBox="0 0 10 14" fill="#ddd"><path d="M5 0a5 5 0 0 1 5 5c0 3.5-5 9-5 9S0 8.5 0 5a5 5 0 0 1 5-5zm0 3a2 2 0 1 0 0 4 2 2 0 0 0 0-4z"/></svg></div>
<div class="abs info-text" style="top:3070px">Ashwood Realty Group<br>48 Linden Ave, Maple Ridge,<br>WI 53201, USA</div>
<div class="abs info-icon" style="top:3175px"><svg width="14" height="14" viewBox="0 0 24 24" fill="#ddd"><path d="M6.6 10.8a15 15 0 0 0 6.6 6.6l2.2-2.2a1 1 0 0 1 1-.25 11.4 11.4 0 0 0 3.6.57 1 1 0 0 1 1 1V20a1 1 0 0 1-1 1A17 17 0 0 1 3 4a1 1 0 0 1 1-1h3.5a1 1 0 0 1 1 1c0 1.25.2 2.45.57 3.57a1 1 0 0 1-.25 1z"/></svg></div>
<div class="abs info-text" style="top:3180px">1 555 010 0199</div>
<div class="abs info-icon" style="top:3238px"><svg width="14" height="14" viewBox="0 0 14 14" fill="#ddd"><rect x="3" y="0" width="8" height="4"/><rect x="0" y="5" width="14" height="6" rx="1"/><rect x="3" y="9" width="8" height="5"/></svg></div>
<div class="abs info-text" style="top:3243px">1 555 010 0142</div>
<div class="abs info-icon" style="top:3304px"><svg width="14" height="10" viewBox="0 0 14 10" fill="#ddd"><rect width="14" height="10" rx="1"/><path d="M0 1l7 5 7-5" fill="none" stroke="#1b1c1e" stroke-width="1.3"/></svg></div>
<div class="abs info-text" style="top:3309px">info@ashwoodrealty.com</div>

<div class="abs rule"></div>
<div class="abs copyright">Copyrights © 2018, Ashwood Realty Group. All Rights Reserved.</div>
<div class="abs social" style="left:918px"></div>
<div class="abs social" style="left:954px"></div>
<div class="abs social" style="left:990px"></div>
<div class="abs social" style="left:1026px"></div>
<div class="abs social" style="left:1062px"></div>

</body>
</html>
```